hotel's Website

Hotels website redesign for reference pictures, logo etc see http://restwellharbour.co.uk/

1. 2-3 Special offers on the main page.
2. Booking calender
3. Location Map
4. Picture gallery.
5. Journeymarks reviews.
6. short description
7. Social Media sharing.
8 Phone number and address.

Industry/Entity Type

Hotel

Requirements
Must have
• 1. 2-3 Special offers on the main page.
2. Booking calender
3. Location Map
4. Picture gallery.
5. Journeymarks reviews.
6. short description
7. Social Media sharing.

```html
<!DOCTYPE html>
<html lang="en">
<head>
<meta charset="utf-8">
<title>Restwell Harbour Inn</title>
<link href="https://fonts.googleapis.com/css2?family=Open+Sans:wght@300;400;600;700&family=Noto+Serif:wght@400;700&display=swap" rel="stylesheet">
<style>
:root{
  --yellow:#e2bc0a;
  --yellow-dark:#b9970a;
  --red:#b5161a;
  --red-dark:#8e0f12;
  --ink:#2b2b2b;
  --muted:#6b6b6b;
  --paper:#efece4;
  --grey-bg:#e3e1e1;
  --footer:#1d1d1d;
  --footer-line:#2f2f2f;
  --caption:#7b726e;
  --white:#ffffff;
}
*{box-sizing:border-box;margin:0;padding:0}
html,body{width:1200px;height:2824px;overflow:hidden}
body{position:relative;font-family:"Open Sans",Arial,sans-serif;color:var(--ink);background:var(--paper)}
.abs{position:absolute}
svg{display:block}

/* header & hero */
.hero{left:0;top:0;width:1200px;height:348px;background:linear-gradient(100deg,#d8cfc0 0%,#9f9486 35%,#6b5f55 55%,#3c3a3a 75%,#8a8076 100%)}
.topbar{left:0;top:0;width:1200px;height:28px;background:rgba(40,40,40,.85)}
.topbar .contact{top:5px;font-size:11px;color:#e8e8e8;display:flex;align-items:center;gap:8px;white-space:nowrap}
.ico-box{width:18px;height:18px;background:#6a6a6a;border-radius:2px;display:flex;align-items:center;justify-content:center}
.social{top:3px;left:756px;display:flex;gap:6px}
.social span{width:22px;height:22px;border-radius:2px;display:block}
.social .s1{background:#3aa9dd}.social .s2{background:#3b5b98}.social .s3{background:#d6402c}
.location-link{right:14px;top:6px;font-size:10px;color:#eee;display:flex;gap:6px;align-items:center;white-space:nowrap}
.navband{left:0;top:28px;width:1200px;height:68px;background:rgba(30,30,30,.55)}
.brand{left:256px;top:28px;width:58px;height:66px;background:#1f4f95;color:var(--white);font-size:10px;font-weight:700;display:flex;align-items:center;justify-content:center;text-align:center;line-height:1.2}
.nav{top:60px;left:336px;display:flex;align-items:center;font-size:10px;color:#f2f2f2;text-transform:uppercase;font-weight:600;white-space:nowrap}
.nav a{color:inherit;text-decoration:none;margin-right:26px}
.nav a.active{color:var(--yellow)}
.hero-title{left:256px;top:136px;width:308px;height:42px;background:rgba(226,188,10,.85);color:var(--white);font-size:25px;font-weight:300;padding:4px 0 0 24px;white-space:nowrap}
.hero-sub{left:300px;top:188px;width:304px;height:22px;background:rgba(30,30,30,.85);color:#eee;font-size:14px;padding:1px 0 0 10px;white-space:nowrap}
.hero-btn{left:454px;top:218px;width:126px;height:36px;background:var(--red);color:var(--white);font-size:19px;text-align:center;line-height:36px;border-radius:2px;white-space:nowrap}
.arrow-tab{top:146px;width:34px;height:54px;background:rgba(226,188,10,.9);display:flex;align-items:center;justify-content:center}

/* calendar */
.calendar{left:256px;top:236px;width:156px;height:148px;background:#f4f2ee;border:1px solid #cfcac0;font-size:9px}
.cal-head{height:18px;background:#3a3a3a;color:#eee;display:flex;justify-content:space-between;align-items:center;padding:0 8px}
.cal-grid{display:grid;grid-template-columns:repeat(7,1fr);gap:2px;padding:4px}
.cal-grid span{text-align:center;height:14px;line-height:14px;background:#e3dfd7;color:#333}
.cal-grid .dow{background:none;font-size:7px;color:#666}
.cal-grid .off{color:#aaa}
.cal-grid .sel{background:var(--yellow);color:var(--white)}

/* booking bar */
.book-field{top:386px;height:34px;background:var(--yellow);border:2px solid var(--yellow-dark);font-size:11px;color:#333;display:flex;align-items:center;justify-content:space-between;padding:0 6px 0 18px;white-space:nowrap}
.book-field i{font-style:normal;width:26px;height:24px;background:#d3ad07;display:block}
.check-btn{left:788px;top:386px;width:148px;height:34px;background:#1e1e1e;color:#eee;font-size:11px;text-align:center;line-height:30px;border:2px solid var(--red);white-space:nowrap}

/* offers */
.offer{top:460px;width:196px}
.offer .photo{height:172px;border:6px solid var(--white);box-shadow:0 2px 4px rgba(0,0,0,.3)}
.offer h3{font-family:"Noto Serif",Georgia,serif;color:var(--red);font-size:16px;text-align:center;line-height:20px;margin-top:18px}
.offer p{font-size:11px;color:#444;text-align:center;margin-top:6px;line-height:16px}
.offer .btn{display:flex;margin:12px auto 0;width:124px;height:32px;background:var(--yellow);border:2px solid var(--yellow-dark);color:var(--white);font-size:15px;font-weight:700;align-items:center;white-space:nowrap}
.offer .btn b{flex:0 0 30px;height:28px;background:#c59f06;display:flex;align-items:center;justify-content:center}
.offer .btn span{flex:1;text-align:center}

/* description band */
.about-band{left:0;top:788px;width:1200px;height:440px;background:linear-gradient(180deg,#4a303b 0%,#3b2530 55%,#5a2a35 100%)}
.about-text{left:266px;top:838px;width:670px;color:#f1ecee;font-size:24px;font-weight:400;line-height:32px;letter-spacing:.2px}
.book-now{left:414px;top:1098px;width:334px;height:68px;background:var(--red);border:3px solid var(--red-dark);color:var(--white);font-size:38px;font-weight:700;display:flex;align-items:center;justify-content:center;gap:16px;white-space:nowrap}

/* reviews */
.reviews-title{left:256px;top:1250px;width:688px;height:46px;background:var(--yellow);display:flex;align-items:center;gap:16px;padding-left:6px}
.reviews-title .badge{width:64px;height:40px;background:#2a2a2a;border-radius:4px}
.reviews-title h2{font-family:"Noto Serif",Georgia,serif;font-size:19px;font-weight:700;color:#1d1d1d;letter-spacing:.4px;white-space:nowrap}
.review{left:268px;width:660px}
.review .stars{color:var(--yellow);font-size:15px;letter-spacing:1px}
.review .name{left:76px;top:0;font-weight:700;font-size:15px}
.review .date{left:76px;top:26px;font-size:10px;color:var(--muted)}
.review .body{left:154px;top:20px;width:510px;font-size:10.5px;line-height:16px;color:#555}
.rule{left:256px;width:688px;height:1px;background:#d4cfc4}
.view-all{left:796px;top:1472px;width:120px;height:36px;background:var(--red);color:var(--white);font-size:17px;display:flex;align-items:center;justify-content:center;gap:10px;white-space:nowrap}
.view-all span{width:26px;height:16px;background:var(--white);border-radius:8px;display:block}

/* events & video */
.sec-tag{top:1536px;height:30px;background:var(--yellow);font-family:"Noto Serif",Georgia,serif;font-size:18px;color:#222;padding:4px 0 0 10px;white-space:nowrap}
.event{left:256px;width:342px;height:114px;background:#e0dbcf;border:1px solid #d2ccbe}
.event .day{left:6px;top:10px;width:34px;height:24px;background:var(--white);font-size:12px;text-align:center;line-height:24px}
.event .mon{left:6px;top:34px;width:34px;height:14px;background:var(--yellow);color:var(--white);font-size:8px;font-weight:700;text-align:center;line-height:14px}
.event .thumb{left:54px;top:10px;width:66px;height:66px;border:3px solid var(--white)}
.event h4{left:132px;top:6px;font-size:13px;font-weight:400;white-space:nowrap}
.event .meta{left:132px;top:26px;font-size:9px;color:#888}
.event p{left:132px;top:42px;width:200px;font-size:8.5px;line-height:12px;color:#666}
.event .more{right:14px;bottom:6px;font-size:8.5px;color:var(--red)}
.view-link{left:880px;top:1546px;font-size:11px;color:#222;white-space:nowrap}
.video{left:618px;top:1604px;width:326px;height:180px;background:linear-gradient(180deg,#10121c 0%,#1d2840 60%,#3a2a3a 100%)}
.video .title{left:10px;top:6px;color:#eee;font-size:12px;white-space:nowrap}
.video .play{left:140px;top:72px;width:44px;height:30px;background:var(--red);border-radius:7px;display:flex;align-items:center;justify-content:center}
.video .bar{left:0;bottom:0;width:326px;height:16px;background:#111}

/* gallery */
.gallery{left:0;top:1840px;width:1200px;height:654px;background:var(--grey-bg)}
.gallery-title{left:0;top:1870px;width:1200px;display:flex;justify-content:center;align-items:center;gap:14px;font-family:"Noto Serif",Georgia,serif;font-size:28px;font-weight:700;color:var(--red);letter-spacing:1px}
.gallery-title i{width:26px;height:26px;border-radius:50%;background:var(--yellow);display:block}
.tile{width:220px;height:186px;border-radius:3px;overflow:hidden}
.tile .photo{height:146px}
.tile .cap{height:40px;background:var(--caption);color:var(--white);padding:3px 10px;white-space:nowrap}
.tile .cap b{display:block;font-weight:400;font-size:15px;line-height:18px}
.tile .cap small{font-size:9.5px;color:#eee}
.tile.active .cap{background:var(--yellow)}
.tile.active .cap b,.tile.active .cap small{color:#222}
.zoom{left:96px;top:58px;width:30px;height:30px;border-radius:50%;background:#222}

/* twitter band & footer */
.tweet-band{left:0;top:2494px;width:1200px;height:60px;background:var(--yellow);border-top:2px solid #c9a509}
.tweet-band i{left:264px;top:16px;width:28px;height:28px;border-radius:50%;background:#222;display:block}
.tweet-band p{left:326px;top:20px;font-size:12px;color:#222;white-space:nowrap}
.footer{left:0;top:2554px;width:1200px;height:270px;background:var(--footer)}
.footer h5{font-family:"Noto Serif",Georgia,serif;font-weight:400;font-size:13px;color:#8a8a8a;letter-spacing:.5px;border-bottom:1px solid var(--footer-line);padding-bottom:6px;white-space:nowrap}
.f-col{top:2608px}
.f-col p,.f-col li{font-size:11px;line-height:16px;color:#ddd;list-style:none}
.f-col li{font-size:10px;line-height:17px;white-space:nowrap}
.f-more{top:2752px;width:60px;height:24px;background:var(--red);color:var(--white);font-size:12px;text-align:center;line-height:24px;white-space:nowrap}
.thumbs{display:grid;grid-template-columns:repeat(3,46px);gap:10px;margin-top:14px}
.thumbs span{height:44px;border:2px solid var(--yellow);display:block}
.contact-line{font-size:10px!important;line-height:14px!important;white-space:nowrap}
.bottombar{left:0;top:2788px;width:1200px;height:36px;background:#151515;border-top:1px solid var(--footer-line)}
.bottombar p{left:256px;top:10px;font-size:10px;color:#888}
.bottombar .dots{left:764px;top:10px;display:flex;gap:18px}
.bottombar .dots span{width:14px;height:14px;border-radius:50%;background:#555;display:block}
</style>
</head>
<body>

<!-- hero -->
<div class="abs hero" role="img" aria-label="Photo of a smiling couple on a scooter in front of Georgian townhouses"></div>
<div class="abs topbar">
  <div class="abs contact" style="left:256px">
    <span class="ico-box"><svg width="10" height="10" viewBox="0 0 10 10"><path d="M2 1l2 2-1 1.2c.6 1.2 1.5 2.1 2.7 2.7L7 6l2 2-1.2 1.2C4.5 9 1 5.5.8 2.2z" fill="#fff"/></svg></span>
    +44 (0) 20 7946 0123
  </div>
  <div class="abs contact" style="left:398px">
    <span class="ico-box"><svg width="10" height="8" viewBox="0 0 10 8"><rect x=".5" y=".5" width="9" height="7" fill="none" stroke="#fff"/><path d="M.5.5L5 4.5 9.5.5" fill="none" stroke="#fff"/></svg></span>
    info@restwellharbour.co.uk
  </div>
  <div class="abs social"><span class="s1"></span><span class="s2"></span><span class="s3"></span></div>
  <div class="abs location-link">Click Here To View Location
    <svg width="26" height="10" viewBox="0 0 26 10"><path d="M0 5h20M16 1l4 4-4 4" stroke="#e2bc0a" stroke-width="2" fill="none"/></svg>
    <svg width="10" height="14" viewBox="0 0 10 14"><path d="M5 14S0 7 0 5a5 5 0 0110 0c0 2-5 9-5 9z" fill="#e2bc0a"/><circle cx="5" cy="5" r="2" fill="#333"/></svg>
  </div>
</div>
<div class="abs navband"></div>
<div class="abs brand">Restwell<br>Harbour Inn</div>
<nav class="abs nav">
  <a>Home</a><a class="active">Bedrooms</a><a>Attractions</a><a>London Events</a><a>Special Offers</a><a>Photos</a><a>Videos</a><a>Contact</a>
  <svg width="12" height="12" viewBox="0 0 12 12"><circle cx="5" cy="5" r="3.8" stroke="#fff" stroke-width="1.6" fill="none"/><path d="M8 8l3.5 3.5" stroke="#fff" stroke-width="1.8"/></svg>
</nav>
<div class="abs hero-title">Lorem ipsum dolor sit</div>
<div class="abs hero-sub">Sed ut perspiciatis unde omnis iste natus</div>
<div class="abs hero-btn">Click Here</div>
<div class="abs arrow-tab" style="left:0"><svg width="12" height="18" viewBox="0 0 12 18"><path d="M10 2L3 9l7 7" stroke="#fff" stroke-width="2.5" fill="none"/></svg></div>
<div class="abs arrow-tab" style="right:0;background:rgba(60,60,60,.7)"><svg width="12" height="18" viewBox="0 0 12 18"><path d="M2 2l7 7-7 7" stroke="#fff" stroke-width="2.5" fill="none"/></svg></div>

<!-- booking calendar -->
<div class="abs calendar">
  <div class="cal-head"><span>◂</span><span>December 2013</span><span>▸</span></div>
  <div class="cal-grid">
    <span class="dow">MON</span><span class="dow">TUE</span><span class="dow">WED</span><span class="dow">THU</span><span class="dow">FRI</span><span class="dow">SAT</span><span class="dow">SUN</span>
    <span class="off">30</span><span>1</span><span>2</span><span>3</span><span class="sel">4</span><span>5</span><span>6</span>
    <span>7</span><span>8</span><span>9</span><span>10</span><span>11</span><span>12</span><span>13</span>
    <span>14</span><span>15</span><span>16</span><span>17</span><span>18</span><span>19</span><span>20</span>
    <span>21</span><span>22</span><span>23</span><span>24</span><span>25</span><span>26</span><span>27</span>
    <span>28</span><span>29</span><span>30</span><span>31</span><span class="off">1</span><span class="off">2</span><span class="off">3</span>
  </div>
</div>

<div class="abs book-field" style="left:264px;width:116px">Arrive <i></i></div>
<div class="abs book-field" style="left:402px;width:114px">Depart <i></i></div>
<div class="abs book-field" style="left:544px;width:116px">Guests <i style="background:#fff;width:20px;height:16px"></i></div>
<div class="abs book-field" style="left:676px;width:96px">Room <i style="background:#fff;width:30px;height:16px"></i></div>
<div class="abs check-btn">Check Availability</div>

<!-- special offers -->
<div class="abs offer" style="left:256px">
  <div class="photo" role="img" aria-label="Woman in a spa robe against a patterned wall" style="background:linear-gradient(160deg,#d9b48f,#b77b55 60%,#8a5a45)"></div>
  <h3>25% off on Spa<br>Treatments</h3>
  <p>Stay with us and get 25% off on<br>Spa Treatments.</p>
  <div class="btn"><b><svg width="14" height="14" viewBox="0 0 14 14"><path d="M6 2H1v11h11V8M8 1h5v5M13 1L6 8" stroke="#fff" stroke-width="1.6" fill="none"/></svg></b><span>Get it</span></div>
</div>
<div class="abs offer" style="left:500px">
  <div class="photo" role="img" aria-label="Brightly lit shop front in London" style="background:linear-gradient(160deg,#3a2a55,#a23a3a 55%,#d8a040)"></div>
  <h3>Shopping in<br>London</h3>
  <p>For the ultimate discount sales<br>shopping London is always ...</p>
  <div class="btn"><b><svg width="14" height="14" viewBox="0 0 14 14"><path d="M6 2H1v11h11V8M8 1h5v5M13 1L6 8" stroke="#fff" stroke-width="1.6" fill="none"/></svg></b><span>Shop Now</span></div>
</div>
<div class="abs offer" style="left:750px">
  <div class="photo" role="img" aria-label="Small white hire car on a street" style="background:linear-gradient(160deg,#c9ccd0,#9aa0a6 55%,#6c6f72)"></div>
  <h3>Low Cost<br>Car Hire</h3>
  <p>Driving in central London –<br>Hire a car</p>
  <div class="btn"><b><svg width="14" height="14" viewBox="0 0 14 14"><path d="M6 2H1v11h11V8M8 1h5v5M13 1L6 8" stroke="#fff" stroke-width="1.6" fill="none"/></svg></b><span>Book Now</span></div>
</div>

<!-- short description -->
<div class="abs about-band" role="img" aria-label="Dimly lit hotel bedroom with a double bed and bedside lamps"></div>
<p class="abs about-text">Our tastefully appointed four storey building is comprised of three attractive Georgian style townhouses – beautifully renovated and continuously maintained to provide comfort as well as stylish decor and useful amenities in all rooms. Our Hotel is a non smoking hotel</p>
<div class="abs book-now">Book Now
  <svg width="34" height="30" viewBox="0 0 34 30"><path d="M1 14L33 1 26 29 17 20 13 28 12 18 28 5 10 16z" fill="#fff"/></svg>
</div>

<!-- reviews -->
<div class="abs reviews-title"><span class="badge"></span><h2>SEE WHAT&nbsp; VISTORS ARE WRITING IN JOURNEYMARKS</h2></div>
<div class="abs review" style="top:1306px;height:70px">
  <div class="stars">★★★★</div>
  <div class="abs name">John Doe</div>
  <div class="abs date">Nov 26, 2013</div>
  <p class="abs body">Lorem ipsum dolor sit amet, consectetur adipisicing elit, sed do eiusmod tempor incididunt ut labore et dolore magna aliqua. Ut enim ad minim veniam, quis nostrud exercitation ullamco laboris nisi ut aliquip ex ea commodo consequat.</p>
</div>
<div class="abs rule" style="top:1394px"></div>
<div class="abs review" style="top:1416px;height:70px">
  <div class="stars">★★★★</div>
  <div class="abs name">John Doe</div>
  <div class="abs date">Nov 26, 2013</div>
  <p class="abs body">Lorem ipsum dolor sit amet, consectetur adipisicing elit, sed do eiusmod tempor incididunt ut labore et dolore magna aliqua. Ut enim ad minim veniam, quis nostrud exercitation ullamco laboris nisi ut aliquip ex ea commodo consequat.</p>
</div>
<div class="abs view-all">VIEW ALL <span></span></div>

<!-- events & video -->
<div class="abs sec-tag" style="left:252px;width:218px">LATEST EVENTS</div>
<div class="abs sec-tag" style="left:618px;width:218px">LATEST VIDEOS</div>
<div class="abs view-link">View all ➜</div>

<div class="abs event" style="top:1580px">
  <div class="abs day">01</div><div class="abs mon">NOV</div>
  <div class="abs thumb" role="img" aria-label="Guards parade in red uniforms" style="background:linear-gradient(160deg,#b22a2a,#5a2020)"></div>
  <h4 class="abs">Lorem ipsum dolor</h4>
  <div class="abs meta">10 Comments</div>
  <p class="abs">Neque porro quisquam est, qui dolorem ipsum quia dolor sit amet, consectetur, adipisci velit, sed quia non numquam eius modi tempora incidunt ut labore et dolore magnam aliquam.</p>
  <div class="abs more">Read More ➜</div>
</div>
<div class="abs event" style="top:1704px">
  <div class="abs day">01</div><div class="abs mon">NOV</div>
  <div class="abs thumb" role="img" aria-label="Colourful carnival costume" style="background:linear-gradient(160deg,#2a6fc0,#d83a6a 55%,#e2bc0a)"></div>
  <h4 class="abs">At vero eos et accusamus</h4>
  <div class="abs meta">4 Comments</div>
  <p class="abs">Neque porro quisquam est, qui dolorem ipsum quia dolor sit amet, consectetur, adipisci velit, sed quia non numquam eius modi tempora incidunt ut labore et dolore magnam aliquam.</p>
  <div class="abs more">Read More ➜</div>
</div>

<div class="abs video" role="img" aria-label="Video still of a lit Ferris wheel and fair at night">
  <div class="abs title">2013 Restwell Harbour Inn London Event1</div>
  <div class="abs play"><svg width="12" height="14" viewBox="0 0 12 14"><path d="M0 0l12 7-12 7z" fill="#fff"/></svg></div>
  <div class="abs bar"></div>
</div>

<!-- gallery -->
<div class="abs gallery"></div>
<div class="abs gallery-title"><i></i>GALLERY</div>

<div class="abs tile active" style="left:256px;top:1956px">
  <div class="photo" role="img" aria-label="Hotel bedroom with red bedspread" style="background:linear-gradient(160deg,#c4a476,#8a4a32 60%,#5a3a2a);position:relative"><span class="abs zoom"></span></div>
  <div class="cap"><b>Lorem Ipsum</b><small>Sed ut perspiciatis unde omnis</small></div>
</div>
<div class="abs tile" style="left:490px;top:1956px">
  <div class="photo" role="img" aria-label="Breakfast bar with stools" style="background:linear-gradient(160deg,#e8dcc0,#c9b48a 60%,#8a6a40)"></div>
  <div class="cap"><b>Lorem Ipsum</b><small>Sed ut perspiciatis unde omnis</small></div>
</div>
<div class="abs tile" style="left:724px;top:1956px">
  <div class="photo" role="img" aria-label="Twin bedroom with patterned covers" style="background:linear-gradient(160deg,#5a3a30,#a24a30 55%,#d6b088)"></div>
  <div class="cap"><b>Lorem Ipsum</b><small>Sed ut perspiciatis unde omnis</small></div>
</div>
<div class="abs tile" style="left:256px;top:2156px">
  <div class="photo" role="img" aria-label="Bright bedroom with yellow accents" style="background:linear-gradient(160deg,#d8c8a0,#c9a040 55%,#6a4a30)"></div>
  <div class="cap"><b>Lorem Ipsum</b><small>Sed ut perspiciatis unde omnis</small></div>
</div>
<div class="abs tile" style="left:490px;top:2156px">
  <div class="photo" role="img" aria-label="Breakfast bar with stools" style="background:linear-gradient(160deg,#e8dcc0,#c9b48a 60%,#8a6a40)"></div>
  <div class="cap"><b>Lorem Ipsum</b><small>Sed ut perspiciatis unde omnis</small></div>
</div>
<div class="abs tile" style="left:724px;top:2156px">
  <div class="photo" role="img" aria-label="Twin bedroom with patterned covers" style="background:linear-gradient(160deg,#5a3a30,#a24a30 55%,#d6b088)"></div>
  <div class="cap"><b>Lorem Ipsum</b><small>Sed ut perspiciatis unde omnis</small></div>
</div>

<!-- latest post band -->
<div class="abs tweet-band"><i class="abs"></i><p class="abs">Lorem ipsum dolor sit amet, consectetur adipisicing elit, sed do eiusmod tempor incididunt ut labore</p></div>

<!-- footer -->
<div class="abs footer"></div>
<div class="abs f-col" style="left:256px;width:168px">
  <h5>ABOUT US</h5>
  <p style="margin-top:12px">Sed ut perspiciatis unde omnis iste natus error sit voluptatem accusantium doloremque laudantium, totam rem aperiam, eaque ipsa quae ab illo inventore veritatis et quasi.</p>
</div>
<div class="abs f-more" style="left:346px">More ➜</div>
<div class="abs f-col" style="left:442px;width:160px">
  <h5>ATTRACTIONS</h5>
  <div class="thumbs" role="img" aria-label="Small photos of London attractions">
    <span style="background:#8a3a3a"></span><span style="background:#2a3a6a"></span><span style="background:#c9a040"></span>
    <span style="background:#6a4a3a"></span><span style="background:#3a4a5a"></span><span style="background:#5a6a9a"></span>
  </div>
</div>
<div class="abs f-more" style="left:534px">More ➜</div>
<div class="abs f-col" style="left:620px;width:152px">
  <h5>FROM OUR BLOG</h5>
  <ul style="margin-top:12px">
    <li>| Lorem ipsum dolor sit amet</li><li>| Adipisicing elit, sed do</li><li>| Adipisicing elit, sed do</li><li>| Incididunt ut labore et dolore</li><li>| Quis nostrud exercitation</li>
  </ul>
</div>
<div class="abs f-col" style="left:784px;width:160px">
  <h5>CONTACT</h5>
  <p class="contact-line" style="margin-top:12px">⌖ 42 Quayside Row, Harbourside<br>&nbsp;&nbsp;&nbsp;London HB1 2QA</p>
  <p class="contact-line" style="margin-top:8px">✉ stay@restwellharbour.co.uk</p>
  <p class="contact-line" style="margin-top:8px">☏ + 44 (0) 20 7946 0456<br>&nbsp;&nbsp;&nbsp;Fax + 44 (0) 20 7946 0789</p>
</div>
<div class="abs bottombar">
  <p class="abs">Copyright 2013 Restwell Harbour Inn</p>
  <div class="abs dots"><span></span><span></span><span></span></div>
</div>

</body>
</html>
```